Fresh, modern, fun business card for pediatric dental practice

Need a business card for fresh, modern, fun pediatric dental practice

Clean look that matches our website's font and colors

We prefer the look of curved corners on business cards

Target Market(s)

parents (mothers) of young children, professionals, mid-high class

Industry/Entity Type

Dental

Contact Information for Business Card

Maplebrook Pediatric Dentistry
482 Quarry Lane
Suite 517
Bramton, PA 17560
717.555.0193
www.maplebrookkidsdental.example

Mei-Ran Tsai, DMD
Corinne Walbeck, DMD
(we are working on our email address, but we would like that on the card as well)

Font styles to use
Sans Serif

Requirements
Must have
• All info; we would also like to make cards for individual staff members
• colors from our website and color palatte, attatched
• use same font and design as website for branding
Nice to have
• clean, simple card that has a pop of color
• we would like to see a few designs with our tag line "where smiles get brighter"
• we are not sure if we want to have it on there or not
• we would like to see a few designs incorporating the ribbon graphic on our website where the word WELCOME is

```html
<!DOCTYPE html>
<html lang="en">
<head>
<meta charset="utf-8">
<title>Maplebrook Pediatric Dentistry – Business Card</title>
<link rel="stylesheet" href="https://fonts.googleapis.com/css2?family=Raleway:wght@500&family=Lato:wght@400&display=swap">
<style>
  :root {
    --stage: #1f1f1f;
    --card-white: #ffffff;
    --magenta: #cc2a8f;
    --magenta-text: #c4178a;
    --sun-yellow: #f6b21c;
    --ink: #2b2b2b;
  }
  html, body {
    margin: 0;
    padding: 0;
    width: 1200px;
    height: 900px;
    overflow: hidden;
    background: var(--stage);
  }
  .canvas {
    position: relative;
    width: 1200px;
    height: 900px;
    background: var(--stage);
  }
  .card {
    position: absolute;
    top: 306px;
    width: 440px;
    height: 271px;
    border-radius: 12px;
    overflow: hidden;
    box-shadow: 0 3px 6px rgba(0, 0, 0, 0.45);
  }
  .card--front {
    left: 149px;
    background: var(--card-white);
  }
  .card--back {
    left: 608px;
    background: var(--magenta);
  }
  .back-fill {
    position: absolute;
    inset: 0;
    background: var(--magenta);
  }
  .brand {
    position: absolute;
    left: 24px;
    top: 50px;
  }
  .brand__dot {
    display: block;
    width: 26px;
    height: 26px;
    border-radius: 50%;
    background: var(--sun-yellow);
    margin: 0 0 18px 100px;
  }
  .brand__name {
    margin: 0;
    font-family: "Raleway", sans-serif;
    font-weight: 500;
    font-size: 24px;
    line-height: 1.2;
    color: var(--sun-yellow);
  }
  .doctors {
    position: absolute;
    right: 19px;
    top: 28px;
    margin: 0;
    text-align: right;
    font-family: "Raleway", sans-serif;
    font-weight: 500;
    font-size: 16px;
    line-height: 23px;
    color: var(--magenta-text);
  }
  .address {
    position: absolute;
    right: 23px;
    top: 154px;
    margin: 0;
    text-align: right;
    font-family: "Lato", sans-serif;
    font-style: normal;
    font-size: 13px;
    line-height: 16px;
    color: var(--ink);
  }
  .contact {
    position: absolute;
    right: 20px;
    top: 201px;
    margin: 0;
    padding: 0;
    list-style: none;
    font-family: "Lato", sans-serif;
    font-size: 13px;
    line-height: 16px;
    color: var(--ink);
  }
  .contact__item {
    display: flex;
    justify-content: flex-end;
    align-items: center;
    gap: 4px;
  }
  .contact__icon {
    width: 10px;
    height: 10px;
    flex: none;
  }
</style>
</head>
<body>
  <main class="canvas">
    <section class="card card--front" aria-label="Business card front">
      <div class="brand">
        <span class="brand__dot" aria-hidden="true"></span>
        <p class="brand__name">Maplebrook<br>Pediatric Dentistry</p>
      </div>

      <p class="doctors">Mei-Ran Tsai, DMD<br>Corinne Walbeck, DMD</p>

      <address class="address">482 Quarry Lane<br>Suite 517&nbsp; Bramton, PA 17560</address>

      <ul class="contact">
        <li class="contact__item">
          <span>717.555.0193</span>
          <svg class="contact__icon" viewBox="0 0 10 10" aria-hidden="true">
            <path d="M1 4.2c0-1.4 1.8-2.2 4-2.2s4 .8 4 2.2v.6H7V3.9H3v.9H1z M2.4 5.2h5.2L8.6 9H1.4z" fill="var(--sun-yellow)"/>
          </svg>
        </li>
        <li class="contact__item">
          <span>info@maplebrookkidsdental.example</span>
          <svg class="contact__icon" viewBox="0 0 10 10" aria-hidden="true">
            <rect x="0.5" y="2" width="9" height="6.5" fill="var(--sun-yellow)"/>
            <path d="M0.8 2.3 5 5.6 9.2 2.3" fill="none" stroke="#fff" stroke-width="0.9"/>
          </svg>
        </li>
        <li class="contact__item">
          <span>www.maplebrookkidsdental.example</span>
          <svg class="contact__icon" viewBox="0 0 10 10" aria-hidden="true">
            <circle cx="5" cy="5" r="4.6" fill="var(--sun-yellow)"/>
            <path d="M3 3.2c1 .3 1.3 1.3 2.2 1.4.6.1.5 1.2-.1 1.6M6.8 6.6c.3-.7 1-.9 1.6-.7" fill="none" stroke="#fff" stroke-width="0.8"/>
          </svg>
        </li>
      </ul>
    </section>

    <section class="card card--back" aria-label="Business card back">
      <div class="back-fill" role="img" aria-label="Magenta card back with a repeating pattern of light spiral sun motifs and a white sun mark at the centre"></div>
    </section>
  </main>
</body>
</html>
```